Redesign Website - Current one too plain

The description is in the uploaded file. Please let me know if you need any more information. I'd prefer it if someone could implement the design to a WordPress site but the best design will win, regardless.
I would like the forms to look nice as well
UPDATE:
I don't think we can use the images that I provided, I think they make the site look a bit 'cheap' and I really don't know how to replace them. One thought I have had is to make the "Simple, Unique, Effective" a second feature on the right side of the page with the search on the left
Target Market(s)
Small companies, private sellers of cars and people who rent their caravan/holiday home out
Industry/Entity Type
Advertising
Number of Pages Required
3 page
Colors
Designer to choose colors to be used in the design.
Look and feel
Each slider illustrates characteristics of the customer's brand and the style your logo design should communicate.

```html
<!DOCTYPE html>
<html lang="en">
<head>
<meta charset="UTF-8">
<title>Zelviq — Get In Touch</title>
<link href="https://fonts.googleapis.com/css2?family=Outfit:wght@300;400;500;600&family=Roboto:wght@700&display=swap" rel="stylesheet">
<style>
  :root {
    --ink: #111111;
    --muted: #b3b3b3;
    --field: #f2f2f2;
    --field-text: #8a8a8a;
    --dark: #2b2b2b;
    --accent: #ddff00;
    --paper: #ffffff;
    --photo-top: #3f5a3a;
    --photo-mid: #8c8a7a;
    --photo-low: #4a4a48;
  }
  * { margin: 0; padding: 0; box-sizing: border-box; }
  html, body { width: 1200px; height: 800px; overflow: hidden; background: var(--paper); }
  body { position: relative; font-family: "Outfit", sans-serif; color: var(--ink); }

  .brand {
    position: absolute; left: 89px; top: 42px;
    display: flex; align-items: center; gap: 12px;
    font-size: 28px; font-weight: 400; letter-spacing: 3px; color: #3a3a3a;
  }
  .brand-mark { width: 34px; height: 34px; border-radius: 50%; background: #2e2e2e; }

  .main-nav a {
    position: absolute; top: 49px; font-size: 16px; font-weight: 400;
    color: var(--ink); text-decoration: none;
  }
  .nav-home { left: 548px; }
  .nav-advertise { left: 648px; }
  .nav-contact { left: 769px; }
  .nav-register { left: 882px; }
  .login-button {
    position: absolute; left: 978px; top: 40px; width: 133px; height: 44px;
    background: var(--dark); color: #fff; border-radius: 8px;
    display: flex; align-items: center; justify-content: center;
    font-size: 17px; font-weight: 500; text-decoration: none;
  }

  .hero-photo {
    position: absolute; left: 0; top: 125px; width: 661px; height: 578px;
    border-radius: 0 24px 24px 0;
    background: linear-gradient(180deg, var(--photo-top) 0%, #5b6f4c 35%, var(--photo-mid) 60%, #d9d4c8 72%, var(--photo-low) 100%);
  }

  .contact-heading {
    position: absolute; left: 733px; top: 232px;
    font-family: "Roboto", sans-serif; font-weight: 700; font-size: 35px;
  }
  .field-label {
    position: absolute; font-size: 16px; font-weight: 300; color: var(--muted);
  }
  .field {
    position: absolute; background: var(--field); border-radius: 3px;
    font-size: 9px; color: var(--field-text); padding-left: 13px;
    display: flex; align-items: center;
  }
  .field-message { align-items: flex-start; padding-top: 11px; }

  .submit-button {
    position: absolute; left: 733px; top: 543px; width: 151px; height: 44px;
    background: var(--accent); border-radius: 8px;
    display: flex; align-items: center; justify-content: center;
    font-size: 21px; font-weight: 500; color: var(--ink);
  }

  .site-footer {
    position: absolute; left: 0; top: 755px; width: 1200px; height: 45px;
    border-top: 1px solid #222;
    display: flex; align-items: center; justify-content: center;
    font-size: 18px; font-weight: 400;
  }
  .site-footer strong { font-weight: 600; margin: 0 5px; }
</style>
</head>
<body>
  <header>
    <div class="brand"><span class="brand-mark"></span>ZELVIQ</div>
    <nav class="main-nav">
      <a class="nav-home" href="#">Home</a>
      <a class="nav-advertise" href="#">Advistise</a>
      <a class="nav-contact" href="#">Contact</a>
      <a class="nav-register" href="#">Register</a>
    </nav>
    <a class="login-button" href="#">Login</a>
  </header>

  <div class="hero-photo" role="img" aria-label="Photo of a white motorhome parked among pine trees"></div>

  <section class="contact-form">
    <h1 class="contact-heading">Get In touch</h1>

    <span class="field-label" style="left:733px; top:287px;">First Name</span>
    <div class="field" style="left:733px; top:310px; width:178px; height:31px;">Enter your Name</div>

    <span class="field-label" style="left:933px; top:287px;">Last Name</span>
    <div class="field" style="left:933px; top:310px; width:178px; height:31px;">Enter your Name</div>

    <span class="field-label" style="left:733px; top:352px;">Email Address</span>
    <div class="field" style="left:733px; top:375px; width:378px; height:31px;">Enter your Name</div>

    <span class="field-label" style="left:733px; top:414px;">Message</span>
    <div class="field field-message" style="left:733px; top:437px; width:378px; height:82px;">Typer here</div>

    <div class="submit-button">Submit</div>
  </section>

  <footer class="site-footer">© 2023 <strong>ZELVIQ</strong>. All Rights Reserved</footer>
</body>
</html>
```